Deisgn A Manual Cover for an Australian Health Training Company

We are looking for an A4 Front of Manual Cover Design for a comprehensive administrative training manual to be launched soon in Australia.

The title of the book is :

"Drafting, Shaping and Shipping Office Paperwork"

for the Australian Medical Office (smaller font)

Written and compiled by Mel Dobrik

Target Market(s)

25-45 year old medical administrative students (usually female)

Industry/Entity Type

It Company

Font styles to use
Serif

Colors
3176b5
f68d4c
33b8a4
fffbf0

Requirements
Must have
• University like perhaps
• Human element (picture/s of people)
• About the concept of designing and producing documents in a health setting (this can be entirely conceptual).
• Conceptual design would be considered
• Appealing

```html
<!DOCTYPE html>
<html lang="en">
<head>
<meta charset="utf-8">
<title>Drafting, Shaping and Shipping Office Paperwork — Manual Cover</title>
<link rel="stylesheet" href="https://fonts.googleapis.com/css2?family=Cinzel:wght@400;500;600&family=Marcellus&display=swap">
<style>
  :root {
    --title-blue: #1f4f9e;
    --sub-navy: #1d3a6b;
    --accent-red: #e5362b;
    --rule-red: #e8533f;
    --bg-light: #ffffff;
    --bg-edge: #d9d9db;
    --crest-navy: #243c66;
    --coat-white: #f4f6f9;
    --scrub-blue: #8fb3d6;
    --scrub-deep: #5f8fc0;
  }
  * { margin: 0; padding: 0; box-sizing: border-box; }
  html, body { width: 927px; height: 1200px; overflow: hidden; }
  body { background: var(--bg-edge); }
  .cover {
    position: relative;
    width: 927px;
    height: 1200px;
    overflow: hidden;
    background: radial-gradient(ellipse 75% 65% at 50% 45%, var(--bg-light) 0%, #f7f7f8 45%, var(--bg-edge) 100%);
  }
  .cover-title {
    position: absolute;
    top: 26px;
    left: 0;
    width: 100%;
    text-align: center;
    font-family: "Cinzel", serif;
    font-weight: 600;
    font-size: 68px;
    line-height: 76px;
    letter-spacing: 1.5px;
    color: var(--title-blue);
    text-transform: uppercase;
  }
  .cover-subtitle {
    position: absolute;
    top: 264px;
    left: 30px;
    width: 867px;
    display: flex;
    align-items: center;
    gap: 14px;
  }
  .cover-subtitle .rule {
    flex: 1;
    height: 2px;
    background: var(--rule-red);
  }
  .cover-subtitle .text {
    font-family: "Marcellus", serif;
    font-size: 28px;
    letter-spacing: 1px;
    color: var(--sub-navy);
    white-space: nowrap;
  }
  .publisher {
    position: absolute;
    top: 344px;
    left: 0;
    width: 100%;
    display: flex;
    flex-direction: column;
    align-items: center;
    gap: 8px;
  }
  .publisher .name {
    font-family: "Marcellus", serif;
    font-size: 19px;
    letter-spacing: 1.5px;
    color: var(--crest-navy);
    text-transform: uppercase;
    text-align: center;
    line-height: 21px;
  }
  .publisher .mark {
    width: 88px;
    height: 88px;
    background: var(--crest-navy);
  }
  .team-photo {
    position: absolute;
    top: 553px;
    left: 222px;
    width: 500px;
    height: 500px;
    background:
      radial-gradient(ellipse 48% 50% at 50% 52%, rgba(255,255,255,0) 40%, rgba(255,255,255,0) 100%),
      linear-gradient(90deg, var(--coat-white) 0%, var(--scrub-blue) 20%, var(--coat-white) 38%, var(--scrub-deep) 52%, var(--coat-white) 66%, var(--scrub-blue) 82%, var(--coat-white) 100%);
    -webkit-mask-image: radial-gradient(ellipse 50% 50% at 50% 50%, #000 55%, transparent 100%);
    mask-image: radial-gradient(ellipse 50% 50% at 50% 50%, #000 55%, transparent 100%);
    opacity: 0.9;
  }
  .credit {
    position: absolute;
    top: 1050px;
    left: 0;
    width: 100%;
    text-align: center;
    color: var(--accent-red);
  }
  .credit .label {
    font-family: "Marcellus", serif;
    font-size: 34px;
    line-height: 44px;
  }
  .credit .author {
    font-family: "Cinzel", serif;
    font-weight: 400;
    font-size: 78px;
    line-height: 90px;
    letter-spacing: 2px;
    text-transform: uppercase;
  }
</style>
</head>
<body>
  <main class="cover">
    <h1 class="cover-title">Drafting, Shaping<br>and Shipping<br>Office Paperwork</h1>

    <div class="cover-subtitle">
      <span class="rule"></span>
      <span class="text">for the Australian Medical Office</span>
      <span class="rule"></span>
    </div>

    <div class="publisher">
      <span class="name">Harlow Institute<br>of Training</span>
      <span class="mark"></span>
    </div>

    <div class="team-photo" role="img" aria-label="Photograph of a smiling team of seven doctors and nurses in white coats and blue scrubs, some holding blue folders"></div>

    <div class="credit">
      <p class="label">Written &amp; Compiled by</p>
      <p class="author">Mel Dobrik</p>
    </div>
  </main>
</body>
</html>
```